A multi-page brochure that explains our firm ,KVL Wealth Management

We have a current brochure attached but it is a compilation of several items combined into one. We would like this to have the same content but be one complete theme. We are a financial planning form so it needs to have a level of professionalism but also a comfortable approach for clients and showing that was have a lot of resources and experience. We cater mostly to the 55-60+ age community.

We need the front page picture changed. lake themed would be great, like our website www.TheMoskaHouse.com
Just to be clear we use KVL Wealth Management now as our company name. Parent company name is The Moska House LLC. I attached the current mock brochure and our new logos.
Our logo colors are:
KVL WM Logo Colors:

Blue:
HEX: #0f75bc
RGB: rgba(15,117,188,255)

Grey:
HEX: #6d6e71
RGB: rgba(109,110,113,255)

Target Market(s)

High-level individuals that are looking for financial guidance who are 40 years old and up

Industry/Entity Type

Wealth Management

Requirements
Must have
• Clean and crisp
Nice to have
• https://www.bramblestoneplanners.com/wealth-management-brochure , this is a sample we like

```html
<!DOCTYPE html>
<html lang="en">
<head>
<meta charset="utf-8">
<title>KVL Wealth Management Brochure</title>
<link href="https://fonts.googleapis.com/css2?family=Cinzel:wght@400&family=Karla:wght@400;500&display=swap" rel="stylesheet">
<style>
  :root {
    --brand-blue: #0f75bc;
    --brand-grey: #6d6e71;
    --stage: #b3b3b3;
    --paper: #f5f5f5;
    --ink: #333436;
    --white: #ffffff;
  }
  * { box-sizing: border-box; margin: 0; padding: 0; }
  html, body { width: 1200px; height: 565px; overflow: hidden; background: var(--stage); }
  body { position: relative; font-family: 'Karla', Arial, sans-serif; color: var(--ink); }

  .page { position: absolute; top: 14px; width: 376px; height: 532px; background: var(--paper); overflow: hidden; }
  .page--cover { left: 19px; background: var(--brand-blue); }
  .page--specialist { left: 408px; }
  .page--firm { left: 800px; }

  .photo { position: absolute; display: block; }

  .cover-photo { left: 0; top: 0; width: 376px; height: 297px;
    background: linear-gradient(180deg, #d9ecf6 0%, #a9cde2 35%, #5fa9a6 55%, #4f9c9a 68%, #9a8f78 85%, #7c7263 100%); }
  .cover-brand { position: absolute; top: 38px; right: 20px; text-align: right;
    font-family: 'Karla', Arial, sans-serif; font-weight: 500; font-size: 19px; color: var(--brand-blue); letter-spacing: .2px; }
  .cover-tagline { position: absolute; left: 17px; top: 358px; font-size: 11.5px; color: var(--white); letter-spacing: .3px; }
  .cover-headline { position: absolute; left: 17px; top: 390px; width: 350px;
    font-family: 'Cinzel', Georgia, serif; font-weight: 400; font-size: 24.5px; line-height: 33px; color: var(--white); }

  .page-title { position: absolute; left: 19px; top: 46px;
    font-family: 'Cinzel', Georgia, serif; font-size: 14px; color: var(--brand-blue); letter-spacing: .3px; }
  .page-brand { position: absolute; top: 30px; right: 17px;
    font-family: 'Karla', Arial, sans-serif; font-weight: 500; font-size: 10.5px; color: var(--brand-blue); }

  .team-photo { left: 0; top: 71px; width: 376px; height: 210px;
    background: linear-gradient(135deg, #2d3440 0%, #b9a58f 45%, #d8cbb8 70%, #6e7a4a 100%); }
  .specialist-copy { position: absolute; left: 18px; top: 312px; width: 345px; font-size: 7.6px; line-height: 14px; }
  .specialist-copy p + p { margin-top: 17px; }

  .advisor-photo--desk { left: 0; top: 77px; width: 155px; height: 190px;
    background: linear-gradient(160deg, #4a4d55 0%, #8a8f98 40%, #b9c3cc 65%, #5a3f2c 100%); }
  .advisor-photo--office { left: 0; top: 279px; width: 155px; height: 190px;
    background: linear-gradient(160deg, #c9c4b8 0%, #e4dccb 35%, #2e2c30 70%, #6b5a4c 100%); }
  .firm-copy { position: absolute; left: 172px; top: 84px; width: 188px; font-size: 7.5px; line-height: 14px; }
  .firm-copy p + p { margin-top: 8.5px; }
  .principle { font-family: 'Cinzel', Georgia, serif; color: var(--brand-blue); font-size: 7.5px; }

  .page-footer { position: absolute; left: 0; bottom: 0; width: 100%; height: 19px; background: var(--brand-blue);
    color: var(--white); font-size: 7.5px; text-align: right; padding-right: 19px; line-height: 19px; letter-spacing: .2px; }
</style>
</head>
<body>

  <section class="page page--cover">
    <div class="photo cover-photo" role="img" aria-label="Sunny lakeshore with a wooden pier, clear water over rocks and mountains in the distance"></div>
    <div class="cover-brand">KVL Wealth Management</div>
    <p class="cover-tagline">A boutique approach to Wealth Management</p>
    <h1 class="cover-headline">WEALTH MANAGEMENT FOCUSED ON YOUR NEEDS AND VISION</h1>
  </section>

  <section class="page page--specialist">
    <h2 class="page-title">Partner with a Specialist</h2>
    <div class="page-brand">KVL Wealth Management</div>
    <div class="photo team-photo" role="img" aria-label="Smiling team of four advisors gathered around a desk in a bright office"></div>
    <div class="specialist-copy">
      <p>Understanding your unique needs and vision for the future is the starting point for our relationship. Together, we’ll assess where you are financially and where you want to be. Next, we’ll create a comprehensive wealth management plan that addresses your immediate and long-term goals. What about the unpredictable? We’ll plan for the changes that may be ahead, too.</p>
      <p>Exploring the topics of interest presented in this brochure will give you an idea of the depth and breadth of our services. Rest assured that we’ll partner with you throughout the planning process, always circling back to this fundamental question: what’s right for you and your loved ones?</p>
    </div>
    <footer class="page-footer">48 Harbor Lane, Suite 210 | Lakeview, MN 55901</footer>
  </section>

  <section class="page page--firm">
    <h2 class="page-title">Our Firm</h2>
    <div class="page-brand">KVL Wealth Management</div>
    <div class="photo advisor-photo--desk" role="img" aria-label="Advisor seated at a desk with computer monitors by a window"></div>
    <div class="photo advisor-photo--office" role="img" aria-label="Advisor in a suit talking with clients in a warmly lit office"></div>
    <div class="firm-copy">
      <p>The Moska House LLC, established in 1987, is an independent, full-service, financial consulting firm. As we search the marketplace for innovative, strategic solutions, The Moska House is guided by the following principles:</p>
      <p><span class="principle">Service -</span>&nbsp; We seek to anticipate your needs and exceed your expectations in every aspect of our partnership.</p>
      <p><span class="principle">Planning -</span>&nbsp; We collaborate with you by listening, asking questions, educating and helping you make informed decisions to skillfully implement appropriate, effective financial strategies.</p>
      <p><span class="principle">Integrity -</span>&nbsp; We build long-term client relationships and are proud of the integrity and sensitivity we exhibit when working with all our clients.</p>
      <p>The Moska House has created an environment of objectivity and independence in which to provide independent guidance and access to the widest variety of fiscal tools to support your financial goals. Our work complements the services of your existing advisors, including CPAs and attorneys. The degree and sophistication of the plan varies according to your circumstances.</p>
    </div>
    <footer class="page-footer">48 Harbor Lane, Suite 210 | Lakeview, MN 55901</footer>
  </section>

</body>
</html>
```